Carpentry framing business card and logo design

We need a logo that works well with baseball caps, tee shirts and sweat shirts. We are a carpentry framing company specializing in apartment complexes and large residential communities. We work in what is known as the tri state area southeastern Pennsylvania , New Jersey and northern Delaware . We would like to see die signs using the old English letter M and royal blue colors. Also we stress OSHA compliance and safety.

Industry/Entity Type

Residential

Contact Information for Business Card

Valdrick Construction Co Inc
4870 Quillford Lane
Corvell PA 19087
Dale Valdrick
dale1valdrick@norvexmail.com
267-815-0926

```html
<!DOCTYPE html>
<html lang="en">
<head>
<meta charset="utf-8">
<title>Valdrick Construction Co Inc — Business Card</title>
<link rel="stylesheet" href="https://fonts.googleapis.com/css2?family=Jost:wght@400;500;700&display=swap">
<style>
  :root {
    --backdrop: #e6e6e3;
    --card: #f7f6f2;
    --royal-navy: #22306e;
    --card-shadow: rgba(0, 0, 0, 0.12);
  }
  * { box-sizing: border-box; margin: 0; padding: 0; }
  html, body {
    width: 1200px;
    height: 800px;
    overflow: hidden;
    background: var(--backdrop);
  }
  .canvas {
    position: relative;
    width: 1200px;
    height: 800px;
    display: flex;
    align-items: center;
    justify-content: center;
  }
  .business-card {
    position: relative;
    width: 900px;
    height: 514px;
    background: var(--card);
    box-shadow: 0 10px 30px var(--card-shadow);
    color: var(--royal-navy);
    font-family: "Jost", sans-serif;
  }
  .brand {
    position: absolute;
    top: 66px;
    left: 0;
    right: 0;
    display: flex;
    flex-direction: column;
    align-items: center;
    gap: 16px;
  }
  .brand-square {
    width: 92px;
    height: 92px;
    background: var(--royal-navy);
  }
  .brand-name {
    font-weight: 500;
    font-size: 19px;
    letter-spacing: 0.08em;
    text-transform: uppercase;
    white-space: nowrap;
  }
  .holder-name {
    position: absolute;
    top: 282px;
    left: 0;
    right: 0;
    text-align: center;
    font-weight: 700;
    font-size: 46px;
    letter-spacing: 0.01em;
    white-space: nowrap;
  }
  .contact-row {
    position: absolute;
    left: 48px;
    right: 48px;
    bottom: 62px;
    display: flex;
    justify-content: space-between;
    align-items: center;
    font-size: 18px;
    font-weight: 400;
    white-space: nowrap;
  }
  .contact-item {
    display: flex;
    align-items: center;
    gap: 8px;
  }
  .contact-icon {
    width: 18px;
    height: 18px;
    flex: none;
  }
</style>
</head>
<body>
<main class="canvas">
  <article class="business-card">
    <header class="brand">
      <div class="brand-square"></div>
      <p class="brand-name">Valdrick Construction Co Inc</p>
    </header>

    <h1 class="holder-name">Dale Valdrick</h1>

    <footer class="contact-row">
      <p class="contact-item address">4870 Quillford Lane, Corvell PA 19087</p>
      <p class="contact-item email">
        <svg class="contact-icon" viewBox="0 0 18 18" aria-hidden="true">
          <rect x="1.5" y="4" width="15" height="10" fill="none" stroke="currentColor" stroke-width="1.5"/>
          <path d="M1.5 4 L9 10 L16.5 4" fill="none" stroke="currentColor" stroke-width="1.5"/>
        </svg>
        dale1valdrick@norvexmail.com
      </p>
      <p class="contact-item phone">
        <svg class="contact-icon" viewBox="0 0 18 18" aria-hidden="true">
          <rect x="4.5" y="1" width="9" height="16" rx="1.5" fill="none" stroke="currentColor" stroke-width="1.5"/>
          <line x1="7.5" y1="14.2" x2="10.5" y2="14.2" stroke="currentColor" stroke-width="1.5"/>
        </svg>
        267-815-0926
      </p>
    </footer>
  </article>
</main>
</body>
</html>
```